** Wanted ** Wordpress web design for scaffolding rental and construction company

We need a website design and must be functional to show a basic overview of what our company offers as a service. We have a domain name and a logo but we need web design. This web site should have another scaffolding rental page for construction and renovation as well as a quote section where customers can enter their personal information and also upload photos. The site% 26quot; www.brindlework.com% 26quot; should be intuitive, clear and classy ... The logo must be found on the site in several ways.

Target Market(s)

Professional and no professional

Coding

Coded - Design and coding required

Number of Pages Required

3 page

Font styles to use
Serif
Sans Serif
Decorative
Script

Requirements
Must have
• Our logo
Nice to have
• Slogan:% 26quot; The height% 26 # 224; port% 26 # 233; e hand% 26quot;

```html
<!DOCTYPE html>
<html lang="en">
<head>
<meta charset="utf-8">
<title>Brindlework — Scaffolding Rental &amp; Construction</title>
<link rel="stylesheet" href="https://fonts.googleapis.com/css2?family=Lato:wght@400;700&display=swap">
<style>
:root{
  --blue:#1f86cf;
  --orange:#f5861f;
  --black:#000;
  --ink:#2b2b2b;
  --text:#3a3a3a;
  --dark-btn:#262626;
  --footer:#2c2c2c;
  --white:#fff;
}
*{box-sizing:border-box;margin:0;padding:0}
html,body{width:1200px;height:4166px;overflow:hidden}
body{position:relative;font-family:'Lato',sans-serif;color:var(--text);background:var(--white)}
.abs{position:absolute}
.brand{display:flex;align-items:center;gap:10px;color:var(--white);font-weight:700;font-size:26px;letter-spacing:2px}
.brand-mark{width:18px;height:18px;background:var(--blue)}

/* header */
.site-header{left:0;top:0;width:1200px;height:113px;background:var(--black)}
.site-header .brand{position:absolute;left:116px;top:34px}
.phone{position:absolute;left:902px;top:12px;display:flex;align-items:center;gap:18px;color:var(--white);font-size:18px;font-weight:700}
.main-nav{position:absolute;top:67px;left:469px;display:flex;gap:0}
.main-nav a{position:absolute;white-space:nowrap;color:var(--white);font-size:14px;text-decoration:none}
.main-nav a.active{color:var(--blue)}

/* hero */
.hero{left:0;top:113px;width:1200px;height:555px;background:linear-gradient(180deg,#d9a45a 0%,#e49a3c 40%,#8a5a2c 75%,#3c2a1c 100%)}
.hero-panel{left:200px;top:262px;width:799px;height:204px;background:rgba(238,140,40,.72)}
.hero-title{left:0;top:282px;width:1200px;text-align:center;color:var(--white);font-size:48px;font-weight:700}
.hero-text{left:330px;top:352px;width:540px;text-align:center;color:var(--white);font-size:16px;line-height:34px}
.btn{display:flex;align-items:center;justify-content:center;border-radius:26px;font-weight:700;font-size:16px;text-transform:uppercase}
.hero-btn{left:508px;top:433px;width:184px;height:51px;background:var(--orange);color:var(--white);font-size:18px}
.dots{left:570px;top:625px;display:flex;gap:10px}
.dots span{width:12px;height:12px;border-radius:50%;background:var(--white)}
.dots span.on{background:var(--orange);border:3px solid var(--white)}

/* welcome */
.welcome-title{left:112px;top:755px;color:var(--blue);font-size:40px;font-weight:700;line-height:55px}
.welcome-text{left:112px;top:882px;width:598px;font-size:16px;line-height:34.3px;text-align:justify}
.welcome-btn{left:112px;top:1150px;width:152px;height:51px;background:var(--orange);color:var(--white)}
.welcome-art{left:723px;top:794px;width:378px;height:375px}

/* services */
.photo-scaffold{left:0;top:1295px;width:537px;height:438px;background:linear-gradient(135deg,#c9d3dc,#7d8a96 55%,#3d4650)}
.panel-orange{left:537px;top:1295px;width:551px;height:438px;background:var(--orange)}
.panel-blue{left:112px;top:1733px;width:551px;height:439px;background:var(--blue)}
.photo-builders{left:663px;top:1733px;width:537px;height:439px;background:linear-gradient(160deg,#c9dcea,#9fb3c2 50%,#8aa05a 100%)}
.panel-title{color:var(--white);font-size:31px;font-weight:700}
.panel-text{color:var(--white);font-size:16px;line-height:34.2px;text-align:justify}
.btn-dark{background:var(--dark-btn);color:var(--white)}

/* projects */
.section-title{left:0;width:1200px;text-align:center;color:var(--blue);font-size:40px;font-weight:700}
.proj-photo{width:416px;height:260px}
.proj-caption{width:346px;height:121px;background:var(--white);border-bottom:6px solid var(--blue);border-left:6px solid var(--blue);padding:22px 0 0 26px}
.proj-caption h3{font-size:19px;font-weight:400;color:var(--ink);letter-spacing:.5px;margin-bottom:6px}
.proj-caption p{font-size:16px;line-height:25px;color:var(--text)}
.arrow{width:52px;height:49px;background:var(--blue);display:flex;align-items:center;justify-content:center}

/* quick links */
.quick{left:0;top:2836px;width:1200px;height:553px;background:linear-gradient(180deg,#3a3b3d,#4a4440 60%,#5a4a3a)}
.quick-title{color:var(--white)}
.field{background:var(--white);height:67px;display:flex;align-items:center;justify-content:space-between;padding:0 20px 0 26px;font-size:15px;color:#555}
.message{align-items:flex-start;padding-top:22px;height:131px}
.quick-btn{left:524px;top:3281px;width:152px;height:50px;background:var(--white);color:var(--orange)}

/* customers */
.badge{top:3611px;width:178px;height:89px;border:2px solid #cfcfcf;border-radius:3px;display:flex;align-items:center;justify-content:center}
.badge span{width:90px;height:34px;background:#d9d9d9;border-radius:3px}
.more-dots{left:1101px;top:3638px;display:flex;flex-direction:column;gap:6px}
.more-dots i{width:9px;height:9px;border-radius:50%;background:var(--orange)}

/* footer */
.site-footer{left:0;top:3795px;width:1200px;height:371px;background:var(--footer)}
.footer-brand{left:506px;top:3826px;width:189px;height:100px;justify-content:center}
.footer-nav{left:0;top:3975px;width:1200px;display:flex;justify-content:center;gap:29px}
.footer-nav a{color:var(--white);font-size:15px;text-decoration:none}
.social{left:528px;top:4020px;display:flex;gap:13px}
.social span{width:36px;height:36px;border:2px solid var(--white);border-radius:50%}
.copyright{left:0;top:4098px;width:1200px;text-align:center;color:var(--white);font-size:16px}
.rule{top:4109px;height:1px;background:#9a9a9a}
</style>
</head>
<body>

<header class="abs site-header">
  <div class="brand"><span class="brand-mark"></span>BRINDLEWORK</div>
  <div class="phone">
    <svg width="36" height="36" viewBox="0 0 36 36"><circle cx="18" cy="18" r="16" fill="none" stroke="#1f86cf" stroke-width="2"/><path d="M12 10c1-1 2-1 3 0l2 3c.5 1 0 2-1 2.5 1 2.5 3 4.5 5 5.5.5-1 1.5-1.5 2.5-1l3 2c1 1 1 2 0 3l-1.5 1.5c-5 .5-14-8.5-13.5-13.5z" fill="#1f86cf"/></svg>
    555-014-2290
  </div>
  <nav class="main-nav">
    <a class="active" style="left:0">HOME</a>
    <a style="left:74px">FORMWORK</a>
    <a style="left:194px">SCAFFOLDING</a>
    <a style="left:327px">PROJECTS</a>
    <a style="left:428px">SERVICES</a>
    <a style="left:527px">CONTACT US</a>
  </nav>
</header>

<section>
  <div class="abs hero" role="img" aria-label="Construction site with tower cranes at sunset"></div>
  <div class="abs hero-panel"></div>
  <h1 class="abs hero-title">BRINDLEWORK</h1>
  <p class="abs hero-text">Lorem ipsum dolor sit amet, consectetur adipiscing elit, sed do eiusmod tempor incididunt ut labore.</p>
  <div class="abs btn hero-btn">GET STARTED</div>
  <div class="abs dots"><span></span><span class="on"></span><span></span></div>
</section>

<section>
  <h2 class="abs welcome-title">WELCOME TO<br>BRINDLEWORK</h2>
  <p class="abs welcome-text">Lorem ipsum dolor sit amet, consectetur adipiscing elit, sed do eiusmod tempor incididunt ut labore et dolore magna aliqua. Quis ipsum suspendisse ultrices gravida. Risus coLorem ipsum dolor sit amet, consectetur adipiscing elit, sed do eiusmod tempor incididunt ut labore et dolore magna aliqua. Quis ipsum suspendisse ultrices gravida. Risus commodo viverra maecenas accumsan lacus vel facilisis. mmodo viverra maecenas accumsan lacus vel facilisis.</p>
  <div class="abs btn welcome-btn">READ MORE</div>
  <svg class="abs welcome-art" viewBox="0 0 378 375" role="img" aria-label="Diamond-framed photo of construction work at sunset">
    <defs><linearGradient id="sun" x1="0" y1="0" x2="0" y2="1"><stop offset="0" stop-color="#6d5a6a"/><stop offset=".55" stop-color="#e8842e"/><stop offset="1" stop-color="#f3b24a"/></linearGradient></defs>
    <polygon points="189,2 376,188 189,373 2,188" fill="url(#sun)" stroke="#5aa0dc" stroke-width="3"/>
  </svg>
</section>

<section>
  <div class="abs photo-scaffold" role="img" aria-label="Worker carrying materials on scaffolding"></div>
  <div class="abs panel-orange"></div>
  <h2 class="abs panel-title" style="left:603px;top:1358px">SCAFFOLDING RENTAL</h2>
  <p class="abs panel-text" style="left:603px;top:1414px;width:444px">Lorem ipsum dolor sit amet, consectetur adipiscing elit, sed do eiusmod tempor incididunt ut labore et dolore magna aliqua. Quis ipsum suspendisse ultrices gravida. Risus commodo viverra maecenas accumsan lacus vel facilisis. viverra maecenas accumsan lacus vel facilisis.</p>
  <div class="abs btn btn-dark" style="left:598px;top:1615px;width:151px;height:51px">READ MORE</div>

  <div class="abs panel-blue"></div>
  <div class="abs photo-builders" role="img" aria-label="Engineers in hard hats reviewing plans on a building site"></div>
  <h2 class="abs panel-title" style="left:160px;top:1808px">CONSTRUCTION</h2>
  <p class="abs panel-text" style="left:167px;top:1864px;width:444px">Lorem ipsum dolor sit amet, consectetur adipiscing elit, sed do eiusmod tempor incididunt ut labore et dolore magna aliqua. Quis ipsum suspendisse ultrices gravida. Risus commodo viverra maecenas accumsan lacus vel facilisis. viverra maecenas accumsan lacus vel facilisis.</p>
  <div class="abs btn btn-dark" style="left:162px;top:2065px;width:150px;height:50px">READ MORE</div>
</section>

<section>
  <h2 class="abs section-title" style="top:2272px">LATEST PROJECT</h2>
  <div class="abs arrow" style="left:87px;top:2521px"><svg width="22" height="20" viewBox="0 0 22 20"><path d="M20 10H3M10 2 2 10l8 8" fill="none" stroke="#fff" stroke-width="3"/></svg></div>
  <div class="abs proj-photo" style="left:160px;top:2403px;background:linear-gradient(180deg,#3f74c4,#9bb7dc 60%,#8a8a80)" role="img" aria-label="Scaffolding around a building under construction with cranes"></div>
  <div class="abs proj-caption" style="left:212px;top:2612px"><h3>LOREM IPSUM DOLOR SIT</h3><p>Lorem ipsum dolor sit amet,<br>consectetur adipiscing elit, sed do</p></div>
  <div class="abs proj-photo" style="left:616px;top:2403px;background:linear-gradient(180deg,#d9a45a,#e59436 50%,#5a3a22)" role="img" aria-label="Tower cranes over a city at sunset"></div>
  <div class="abs proj-caption" style="left:668px;top:2612px"><h3>LOREM IPSUM DOLOR SIT</h3><p>Lorem ipsum dolor sit amet,<br>consectetur adipiscing elit, sed do</p></div>
  <div class="abs arrow" style="left:1064px;top:2521px"><svg width="22" height="20" viewBox="0 0 22 20"><path d="M2 10h17M12 2l8 8-8 8" fill="none" stroke="#fff" stroke-width="3"/></svg></div>
</section>

<section>
  <div class="abs quick" role="img" aria-label="Dimmed construction site background"></div>
  <h2 class="abs section-title quick-title" style="top:2920px">QUICK LINKS</h2>
  <div class="abs field" style="left:170px;top:3025px;width:268px">NAME*<svg width="18" height="18" viewBox="0 0 18 18"><circle cx="9" cy="5" r="4" fill="#888"/><path d="M1 17c0-5 4-7 8-7s8 2 8 7z" fill="#888"/></svg></div>
  <div class="abs field" style="left:466px;top:3025px;width:268px">EMAIL*<svg width="18" height="14" viewBox="0 0 18 14"><rect width="18" height="14" fill="#888"/><path d="M1 1l8 6 8-6" fill="none" stroke="#fff" stroke-width="1.5"/></svg></div>
  <div class="abs field" style="left:762px;top:3025px;width:268px">UPLOAD PHOTOS*<svg width="18" height="18" viewBox="0 0 18 18"><path d="M9 1 4 6h3v6h4V6h3z" fill="#888"/><rect x="1" y="13" width="16" height="4" fill="#888"/></svg></div>
  <div class="abs field message" style="left:170px;top:3116px;width:860px">MESSAGE</div>
  <div class="abs btn quick-btn">READ MORE</div>
</section>

<section>
  <h2 class="abs section-title" style="top:3483px">OUR CUSTOMERS</h2>
  <div class="abs badge" style="left:113px"><span></span></div>
  <div class="abs badge" style="left:314px"><span></span></div>
  <div class="abs badge" style="left:513px"><span></span></div>
  <div class="abs badge" style="left:711px"><span></span></div>
  <div class="abs badge" style="left:909px"><span></span></div>
  <div class="abs more-dots"><i></i><i></i><i></i></div>
</section>

<footer>
  <div class="abs site-footer"></div>
  <div class="abs brand footer-brand"><span class="brand-mark"></span>BRINDLEWORK</div>
  <nav class="abs footer-nav"><a>HOME</a><a>FORMWORK</a><a>SCAFFOLDING</a><a>PROJECTS</a><a>SERVICES</a><a>CONTACT US</a></nav>
  <div class="abs social"><span></span><span></span><span></span></div>
  <div class="abs rule" style="left:108px;width:337px"></div>
  <p class="abs copyright">Copyrights 2020. All rights reserved</p>
  <div class="abs rule" style="left:752px;width:335px"></div>
</footer>

</body>
</html>
```